product development company BRVEMKO LLC business card

We need a business card design for a company based in Texas called 'BRVEMKO LLC'. Our first product is a illuminated portable ice chest that is called ' Copper Harbor coolers'. Copper harbor coolers is trademarked. I would like to have the copper harbor trademark somewhere on the card as well as the BRVEMKO LLC name.

Target Market(s)

outdoor industry

Industry/Entity Type

Business

Contact Information for Business Card

i would like to have BRVEMKO LLC logo larger than the Copper harbor coolers logo.

Font styles to use
Serif
Sans Serif

```html
<!DOCTYPE html>
<html lang="en">
<head>
<meta charset="utf-8">
<title>BRVEMKO LLC – Business Card</title>
<link rel="stylesheet" href="https://fonts.googleapis.com/css2?family=Montserrat:wght@700&family=Tinos:wght@400;700&display=swap">
<style>
  :root {
    --backdrop: #d9d6d1;
    --card-white: #f7f7f7;
    --panel-grey-light: #c6c6c6;
    --panel-grey: #a8a8a8;
    --ink: #1a1a1a;
    --ink-soft: #6d6d6d;
    --icon-grey: #9c9c9c;
  }
  * { box-sizing: border-box; margin: 0; padding: 0; }
  html, body {
    width: 1200px; height: 780px; overflow: hidden;
    background: var(--backdrop);
  }
  .canvas {
    width: 1200px; height: 780px;
    display: flex; align-items: center; justify-content: center;
  }
  .card {
    position: relative; width: 1000px; height: 572px;
    background: var(--card-white);
    box-shadow: 0 10px 30px rgba(0,0,0,.25);
    overflow: hidden;
  }
  .card-panels { position: absolute; inset: 0; }
  .company {
    position: absolute; left: 70px; top: 78px;
    font-family: "Montserrat", sans-serif; font-weight: 700;
    font-size: 58px; color: var(--ink); line-height: 1;
  }
  .product-mark {
    position: absolute; right: 60px; top: 196px;
    display: flex; align-items: center; gap: 10px;
    font-family: "Montserrat", sans-serif; font-weight: 700;
    font-size: 28px; color: var(--ink); line-height: 1;
  }
  .product-mark .dot {
    width: 28px; height: 28px; border-radius: 50%;
    background: var(--ink);
  }
  .person {
    position: absolute; left: 64px; top: 372px;
    font-family: "Tinos", serif; line-height: 1.15;
  }
  .person-name { font-weight: 700; font-size: 28px; color: var(--ink); text-transform: uppercase; }
  .person-role { font-size: 21px; color: var(--ink-soft); }
  .contact {
    position: absolute; left: 220px; top: 430px;
    font-family: "Tinos", serif; font-style: normal;
    font-size: 22px; color: var(--ink); line-height: 1.3;
  }
  .contact-row { display: flex; align-items: center; gap: 8px; }
  .contact-icon { width: 20px; height: 20px; flex: none; }
  .web {
    position: absolute; left: 620px; top: 526px;
    font-family: "Tinos", serif; font-size: 22px; color: var(--ink);
  }
</style>
</head>
<body>
<main class="canvas">
  <section class="card" aria-label="BRVEMKO LLC business card">
    <svg class="card-panels" viewBox="0 0 1000 572" role="img" aria-label="Soft grey background panels in the top left and bottom right corners">
      <defs>
        <linearGradient id="panelFill" x1="0" y1="0" x2="1" y2="1">
          <stop offset="0" stop-color="#c6c6c6"/>
          <stop offset="1" stop-color="#a8a8a8"/>
        </linearGradient>
      </defs>
      <path d="M0,0 H780 C640,110 520,230 0,350 Z" fill="url(#panelFill)"/>
      <path d="M1000,240 C820,300 760,470 480,572 H1000 Z" fill="url(#panelFill)"/>
    </svg>

    <h1 class="company">BRVEMKO LLC</h1>

    <div class="product-mark"><span class="dot"></span>copper harbor</div>

    <div class="person">
      <div class="person-name">Wade Carver</div>
      <div class="person-role">Maneger</div>
    </div>

    <address class="contact">
      <div>Your Address, 2nd Ste</div>
      <div>Pinecrest, Texas 1234</div>
      <div class="contact-row">
        <svg class="contact-icon" viewBox="0 0 22 22" aria-hidden="true">
          <rect width="22" height="22" fill="var(--icon-grey)"/>
          <path d="M6 5 h3 l1 4 -2 1 a8 8 0 0 0 4 4 l1 -2 4 1 v3 a2 2 0 0 1 -2 1 A12 12 0 0 1 5 7 a2 2 0 0 1 1 -2z" fill="#fff"/>
        </svg>
        <span>123 456 7890</span>
      </div>
      <div class="contact-row">
        <svg class="contact-icon" viewBox="0 0 22 22" aria-hidden="true">
          <rect width="22" height="22" fill="var(--icon-grey)"/>
          <rect x="4" y="6" width="14" height="10" fill="none" stroke="#fff" stroke-width="1.5"/>
          <path d="M4 6 L11 12 L18 6" fill="none" stroke="#fff" stroke-width="1.5"/>
        </svg>
        <span>info@brvemko.com</span>
      </div>
    </address>

    <div class="web">www.brvemko.com</div>
  </section>
</main>
</body>
</html>
```